Briefpapier und Visitenkarten
Zielgruppe
In erster Linie mir selbst.
Aufgabenstellung
Gestaltung von Visitenkarten und Briefpapier.
Visitenkarten: Gestaltung beidseitig und in Pantone Farben
Briefpapier: Gestaltung einseitig und in Pantone Farben
Briefpapier und Visitenkarten sollen ein Design haben.

```html
<!DOCTYPE html>
<html lang="de">
<head>
<meta charset="utf-8">
<title>Korlan Werbeagentur – Visitenkarte</title>
<link rel="stylesheet" href="https://fonts.googleapis.com/css2?family=Arimo:wght@400&display=swap">
<style>
  :root {
    --page: #ffffff;
    --card: #5d5855;
    --ink: #ffffff;
    --ink-soft: #e9e7e5;
    --mark-faint: rgba(255, 255, 255, 0.13);
    --edge: #d8d6d4;
  }
  html, body {
    margin: 0;
    width: 1200px;
    height: 1200px;
    overflow: hidden;
    background: var(--page);
  }
  .canvas {
    position: relative;
    width: 1200px;
    height: 1200px;
  }
  .card {
    position: absolute;
    left: 300px;
    width: 608px;
    height: 392px;
    background: var(--card);
    overflow: hidden;
    box-shadow: 4px 5px 8px rgba(0, 0, 0, 0.28);
    font-family: "Arimo", Arial, sans-serif;
    color: var(--ink);
  }
  .card--front { top: 138px; }
  .card--back  { top: 675px; }

  .front-mark {
    position: absolute;
    left: 232px;
    top: 48px;
    width: 144px;
    height: 144px;
    border-radius: 50%;
    background: var(--ink-soft);
  }
  .front-name {
    position: absolute;
    left: 0;
    right: 0;
    top: 246px;
    text-align: center;
    font-size: 38px;
    line-height: 1;
    letter-spacing: 1px;
    text-transform: uppercase;
  }
  .front-tagline {
    position: absolute;
    left: 0;
    right: 0;
    top: 294px;
    text-align: center;
    font-size: 15px;
    line-height: 1;
    letter-spacing: 4px;
    text-transform: uppercase;
  }

  .back-mark {
    position: absolute;
    left: 385px;
    top: -25px;
    width: 224px;
    height: 224px;
    border-radius: 50%;
    background: var(--mark-faint);
  }
  .back-name {
    position: absolute;
    left: 37px;
    top: 34px;
    font-size: 28px;
    line-height: 1;
    letter-spacing: 1px;
    text-transform: uppercase;
  }
  .contact {
    position: absolute;
    left: 37px;
    font-size: 24px;
    line-height: 40px;
    margin: 0;
    font-style: normal;
  }
  .contact--address { top: 102px; }
  .contact--online  { top: 292px; }
  .back-edge {
    position: absolute;
    left: 0;
    bottom: 0;
    width: 480px;
    height: 5px;
    background: var(--edge);
  }
</style>
</head>
<body>
<main class="canvas">
  <section class="card card--front" aria-label="Vorderseite">
    <div class="front-mark"></div>
    <div class="front-name">Korlan Werbeagentur</div>
    <div class="front-tagline">Ideen mit Wirkung</div>
  </section>

  <section class="card card--back" aria-label="Rückseite">
    <div class="back-mark"></div>
    <div class="back-name">Korlan Werbeagentur</div>
    <address class="contact contact--address">
      Inh. Jonas Korlan<br>
      Lindenweg 14<br>
      D-53842 Talbrück
    </address>
    <p class="contact contact--online">
      E-Mail: korlan@korlanwa.de<br>
      Website: www.korlanwa.de
    </p>
    <div class="back-edge"></div>
  </section>
</main>
</body>
</html>
```